Velvet Lantern rebranding my business with a new business card

I have my new logo and now I need a refresher on my business cards. I really want something fun and fresh. I like black background or anything to make the color pop.
Logo
Name: Velvet Lantern
Contact Info as stated below:
Mira Pellow
555-013-4762
Logo
Name: Velvet Lantern
Mira Pellow
555-013-4762
fb.me/VelvetLanternbyMira
Instagram: @VelvetLanternbyMira

Industry/Entity Type

Business

Contact Information for Business Card

double-sided. Logo on one side. Contact info on the other.

Requirements
Must have
• Logo
• Name: Velvet Lantern
• Contact Info as stated below:
• Mira Pellow
• 555-013-4762
• fb.me/VelvetLanternbyMira
• fb.me/VelvetLanternbyMira

```html
<!DOCTYPE html>
<html lang="en">
<head>
<meta charset="utf-8">
<title>Velvet Lantern – Business Card</title>
<link rel="stylesheet" href="https://fonts.googleapis.com/css2?family=Delius&display=swap">
<style>
  :root {
    --backdrop: #e8e8e8;
    --front-pink: #f4b3b6;
    --back-pink: #f8dbe3;
    --ink: #1f1f1f;
    --ring-pink: #ef9fb3;
    --badge-white: #fdfcfc;
    --shadow: rgba(0, 0, 0, 0.18);
  }
  html, body {
    margin: 0;
    padding: 0;
    width: 1200px;
    height: 576px;
    overflow: hidden;
    background: var(--backdrop);
    font-family: "Delius", "Comic Sans MS", cursive;
    color: var(--ink);
  }
  .stage {
    position: relative;
    width: 1200px;
    height: 576px;
  }
  .card {
    position: absolute;
    top: 138px;
    width: 484px;
    height: 294px;
    border-radius: 13px;
    overflow: hidden;
    box-shadow: 0 2px 6px var(--shadow);
  }
  .card-front { left: 82px; background: var(--front-pink); }
  .card-back { left: 602px; width: 482px; height: 291px; background: var(--back-pink); }

  .card-pattern {
    position: absolute;
    inset: 0;
  }

  .logo-badge {
    position: absolute;
    left: 136px;
    top: 42px;
    width: 212px;
    height: 212px;
  }
  .logo-badge svg { position: absolute; inset: 0; }
  .brand-name {
    position: absolute;
    margin: 0;
    font-weight: 400;
    color: var(--ink);
    text-align: center;
    line-height: 1.1;
  }
  .logo-badge .brand-name {
    left: 0; right: 0;
    top: 82px;
    font-size: 24px;
  }
  .card-back .brand-name {
    left: 50px;
    top: 112px;
    width: 160px;
    font-size: 22px;
  }

  .contact-block {
    position: absolute;
    left: 258px;
    top: 84px;
  }
  .person-name {
    margin: 0;
    font-size: 22px;
    font-weight: 400;
    letter-spacing: 0.3px;
  }
  .person-title {
    margin: 4px 0 0 2px;
    font-size: 11px;
  }
  .contact-list {
    list-style: none;
    margin: 24px 0 0 -8px;
    padding: 0;
  }
  .contact-item {
    display: flex;
    align-items: center;
    gap: 9px;
    font-size: 17px;
    height: 26px;
  }
  .contact-icon { width: 17px; height: 17px; flex: none; }
</style>
</head>
<body>
<main class="stage">

  <section class="card card-front" aria-label="Business card front">
    <div class="card-pattern" role="img" aria-label="Soft pink polka dot background pattern"></div>
    <div class="logo-badge">
      <svg viewBox="0 0 212 212" width="212" height="212" aria-hidden="true">
        <circle cx="106" cy="106" r="104" fill="var(--badge-white)" stroke="var(--ink)" stroke-width="2"/>
        <circle cx="106" cy="106" r="97" fill="none" stroke="var(--ring-pink)" stroke-width="1.5"/>
        <circle cx="106" cy="106" r="94" fill="none" stroke="var(--ring-pink)" stroke-width="1"/>
      </svg>
      <p class="brand-name">Velvet<br>Lantern</p>
    </div>
  </section>

  <section class="card card-back" aria-label="Business card back">
    <div class="card-pattern" role="img" aria-label="Light pink polka dot background pattern"></div>
    <p class="brand-name">Velvet Lantern</p>

    <div class="contact-block">
      <h1 class="person-name">Mira Pellow</h1>
      <p class="person-title">Managing Director</p>
      <ul class="contact-list">
        <li class="contact-item">
          <svg class="contact-icon" viewBox="0 0 17 17" aria-hidden="true">
            <rect x="0.75" y="0.75" width="15.5" height="15.5" rx="3.5" fill="none" stroke="var(--ink)" stroke-width="1.3"/>
            <path d="M5.2 4.2l1.6-.4 1 2.3-1 .8c.5 1.2 1.4 2.1 2.6 2.6l.8-1 2.3 1-.4 1.6c-.2.6-.8.9-1.4.8C7.6 11.5 5.5 9.4 4.9 6.3c-.1-.6.2-1.2.3-2.1z" fill="var(--ink)"/>
          </svg>
          <span>555-013-4762</span>
        </li>
        <li class="contact-item">
          <svg class="contact-icon" viewBox="0 0 17 17" aria-hidden="true">
            <rect x="0.75" y="0.75" width="15.5" height="15.5" rx="3.5" fill="none" stroke="var(--ink)" stroke-width="1.3"/>
          </svg>
          <span>VelvetLanternbyMira</span>
        </li>
      </ul>
    </div>
  </section>

</main>
</body>
</html>
```